Home Building company needs lettering for our truck doors.

We need lettering for our truck doors and tailgate. We are a home building company in the construction industry. The trucks are gray in color and our company colors are dark blue, gray and white. We'd like the following included in the lettering; Our company name is; Brondale Construction Company. My name is Dean L. Forsholm, Builder/Carpenter/Cabinetmaker. Our phone numbers are; 781-555-0147 and 603-555-0193

Construction

• Times New Roman

```html
<!DOCTYPE html>
<html lang="en">
<head>
<meta charset="utf-8">
<title>Brondale Construction Company – Truck Door Lettering</title>
<link rel="stylesheet" href="https://fonts.googleapis.com/css2?family=Tinos:ital,wght@0,400;0,700;1,400&display=swap">
<style>
  :root {
    --ink-navy: #0e2a5f;
    --ground: #ffffff;
  }
  html, body {
    margin: 0;
    padding: 0;
    width: 1200px;
    height: 1169px;
    overflow: hidden;
    background: var(--ground);
  }
  .door-lettering {
    position: relative;
    width: 1200px;
    height: 1169px;
    font-family: "Tinos", "Times New Roman", serif;
    color: var(--ink-navy);
  }
  .lettering-block {
    position: absolute;
    left: 125px;
    top: 300px;
    width: 950px;
    height: 560px;
  }
  .lettering-block > * {
    position: absolute;
    margin: 0;
    line-height: 1;
    white-space: nowrap;
  }
  .company-name {
    left: 0;
    top: 0;
    font-weight: 700;
    font-size: 86px;
    line-height: 113px;
  }
  .owner-name {
    right: 0;
    top: 232px;
    font-style: italic;
    font-size: 78px;
  }
  .trade-title {
    right: 0;
    top: 340px;
    font-size: 47px;
  }
  .phone-numbers {
    left: 0;
    top: 452px;
    font-size: 73px;
  }
</style>
</head>
<body>
  <main class="door-lettering">
    <section class="lettering-block">
      <h1 class="company-name">Brondale<br>Construction Company</h1>
      <p class="owner-name">Dean L. Forsholm</p>
      <p class="trade-title">Builder/Carpenter/Cabinetmaker</p>
      <p class="phone-numbers">781-555-0147 | 603-555-0193</p>
    </section>
  </main>
</body>
</html>
```